Modern & Simple Essential Oils Label

Company Name: Meadowlark Essentials

What we sell: Aromatherapy products, pure therapeutic essential oils.

Design need:
We are looking for a creative and youthful design for the labels used on small essentials oils.

I have two sizes of bottles that I use for essential oils a 5ml bottle and a 15ml bottle. They are dark Amber color glass with black lids. I like the clear labels or mayble a dark brown background. With white or clear lettering with punch of color too! Each oil type is represented by different color. (lavender- purple, lemon - yellow). The label will be the same for all the oils in the two sizes with only a different oil name & coordinating color.
5ml label size should be: 1 " x 2.625"
15ml label size should be: 1.5" x 3.5"

I have some labels that I have had another designer start on, but they aren't quite what I want and missing that something (alot!).. I don't know what. Interest maybe? Lack of design? I dunno.. they are attached. Maybe it's the logo? I don't know! But its gotta change! When I cut out a proof and put a sample on the bottle as I look straight on at the label all I see is a big dot, no logo.. nothing interesting.
Updates

Project Deadline Extended
Reason: Hi! Id like to extend this deadline. Ive been unavailable for a few days due to an illness and Im so far behind! Im feeling MUCH better and looking forward to getting caught up and move with the project. Im not sure how this works, but I attached a list of the oils that we currently have available. And in the list is the idea for the color schemes for the oils. The basic idea is for it to have a wide array of colors, so using different shades of greens, yellows, oranges and so on. So that its like a rainbow. We are not set of that particular color for that particular oil. It was just a idea list of possible colors for oils. Thanks so much!

Target Market(s)

Metro & Modern people. Interested in healthy organic living, Mostly women (some men) 20-45 who are interested in holistic healing.

Industry/Entity Type

It Company

Requirements
Must have
• A reputable look. Clean, organic, crisp, zen or spa-like feel. Modern, youthful appealing label design. Approachable and interesting, not intimidating so that I don't turn away people who are new or not familiar with how to use essential oils.
Should not have
• do NOT want the look to be anywhere close to medicinal, witchy, crafty, hippie, mystical, overly earthy, magical, or voodoo. Do not want it to look like something out of a grandmothers medicine cabinet.

```html
<!DOCTYPE html>
<html lang="en">
<head>
<meta charset="utf-8">
<title>Meadowlark Essentials – Rosemary 15 ml Label</title>
<link rel="stylesheet" href="https://fonts.googleapis.com/css2?family=Archivo+Narrow:wght@400;700&family=Arimo:ital,wght@0,400;1,700&family=Yellowtail&display=swap">
<style>
  :root {
    --page: #ffffff;
    --label: #efecec;
    --accent: #d12e33;
    --ink: #8c8c8c;
    --ink-dark: #7a7a7a;
    --cut: #555555;
    --on-accent: #ffffff;
  }
  * { margin: 0; padding: 0; box-sizing: border-box; }
  html, body { width: 1200px; height: 591px; overflow: hidden; background: var(--page); }
  .canvas { position: relative; width: 1200px; height: 591px; overflow: hidden; }

  .label { position: absolute; left: 75px; top: 68px; width: 1049px; height: 453px; background: var(--label); }

  .cut-mark { position: absolute; left: 600px; width: 1px; background: var(--cut); }
  .cut-mark--top { top: 45px; height: 25px; }
  .cut-mark--bottom { top: 520px; height: 25px; }

  /* Back panel, read sideways */
  .back {
    position: absolute; left: 75px; top: 521px;
    width: 453px; height: 525px;
    transform: rotate(-90deg); transform-origin: top left;
    font-family: "Archivo Narrow", "Arial Narrow", sans-serif; color: var(--ink);
    font-size: 19px; line-height: 24px; white-space: nowrap;
  }
  .facts {
    position: absolute; left: 16px; top: 14px; width: 417px; height: 164px;
    border: 2px solid var(--accent);
  }
  .facts__title { position: absolute; left: 14px; top: 12px; font-size: 22px; font-weight: 700; color: var(--ink-dark); }
  .facts__list { position: absolute; left: 14px; top: 42px; list-style: none; }
  .facts__grade {
    position: absolute; left: 0; bottom: 0; width: 100%; height: 32px;
    background: var(--accent); color: var(--on-accent);
    padding: 4px 10px; font-size: 19px;
  }
  .back__copy { position: absolute; left: 18px; }
  .back__company { top: 190px; line-height: 22px; }
  .back__usage { top: 258px; line-height: 25px; }
  .back__caution { top: 350px; line-height: 25.5px; }
  .back__caution strong { font-weight: 700; }

  /* Front panel */
  .product-name { position: absolute; left: 0; top: 0; width: 1200px; height: 591px; pointer-events: none; }
  .product-name text { font-family: "Yellowtail", cursive; fill: var(--accent); }

  .botanical {
    position: absolute; left: 935px; top: 116px;
    font-family: "Arimo", Arial, sans-serif; font-style: italic; font-weight: 700;
    font-size: 19px; line-height: 26px; color: var(--ink); text-transform: uppercase;
  }

  .volume {
    position: absolute; left: 637px; top: 478px;
    transform: translate(-50%, -50%) rotate(-90deg);
    font-family: "Arimo", Arial, sans-serif; font-size: 28px; color: var(--accent); white-space: nowrap;
  }
  .brand-band {
    position: absolute; left: 657px; top: 440px; width: 467px; height: 81px;
    background: var(--accent);
    display: flex; align-items: center; justify-content: center; gap: 12px;
  }
  .brand-band__dot { width: 10px; height: 10px; border-radius: 50%; background: var(--on-accent); }
  .brand-band__name { font-family: "Arimo", Arial, sans-serif; font-size: 28px; color: var(--on-accent); }
</style>
</head>
<body>
<main class="canvas">
  <div class="label"></div>
  <div class="cut-mark cut-mark--top"></div>
  <div class="cut-mark cut-mark--bottom"></div>

  <section class="back">
    <div class="facts">
      <h2 class="facts__title">Supplemental Facts</h2>
      <ul class="facts__list">
        <li>Serving Size: 1 drop</li>
        <li>Servings Per Container: About 250</li>
        <li>Oil: Rosmarinus Officinalis</li>
      </ul>
      <p class="facts__grade">100% Pure Therapeutic Grade</p>
    </div>
    <p class="back__copy back__company">Meadowlark Essentials<br>P.O. Box 402, Alder Falls, UT 84099</p>
    <p class="back__copy back__usage">For aromatic, topical use. 100% pure<br>therapeutic-grade essential oil. Dilute with a<br>carrier oil before using.</p>
    <p class="back__copy back__caution"><strong>CAUTION</strong>: For External Use Only. Not for<br>Ingestion. Keep away from eyes and mucous<br>membranes. May cause skin sensitivity. If<br>pregnant consult physician before use. Keep<br>out of reach of children. Keep away from flame.</p>
  </section>

  <svg class="product-name" viewBox="0 0 1200 591" aria-labelledby="product-title">
    <title id="product-title">Rosemary</title>
    <text x="655" y="248" font-size="170" textLength="255" lengthAdjust="spacingAndGlyphs" transform="rotate(-4 655 248)">Rose</text>
    <text x="618" y="368" font-size="170" textLength="420" lengthAdjust="spacingAndGlyphs" transform="rotate(-5 618 368)">mary</text>
  </svg>

  <p class="botanical">Rosmarinus<br>Officinalis<br>100% Pure<br>Essential Oil</p>

  <p class="volume">15 ml</p>
  <div class="brand-band">
    <span class="brand-band__dot"></span>
    <span class="brand-band__name">Meadowlark Essentials</span>
  </div>
</main>
</body>
</html>
```